Website for a company offering full serivce charging solutions for electric cars

The company "tanu-werk" (english: "tanu-works") offering all-in-one-solutions for charging infrastructure for electric mobility.

There are four products:
1- Wallboxes for single-family homes
2- Solutions for property devloper/-management for property parking space
3- All-in-one-charging solution for municipalities/communities
4- Solutions for tourism/hotels/holiday appartments

The Website structure:
1. Main Page
2.1. Product Page Single Homes
2.2. Product Page Property Management / Parking
2.3. Product Page Municipality
2.4. Product Page Tourism
3. Contact Form / Request for information
4. Imprint / Legal

The Website should be built on Wordpress with a powerful possibility to simply add/modify specific landing pages.

We would like you to implement the website later and also maintain it if possible, but we would be able to do minor modifications by ourselfs (for A/B-Testing)

The website should be clear and simple, easy to understand.
Target group is mainly B2C without deeper knowledge of that topic.

It should suggest, that we will provide a very simple way to get the charging infrastructure done.

We need a contact form, maybe we will use Hubspot later.

Attached you will find a draft of the main page and a landing page (for 2.2) - it is just the content, please ignore the design. We would love to let you create a suitable design.
Also you will find some drafts a bit different for the same story.

I added also a few stock photos, but they don't need to be used! If you have better ideas, you are welcome!

Industry/Entity Type

Charging/Electric mobility

Number of Pages Required

2 page

Font styles to use
Sans Serif

Requirements
Must have
• Based on Wordpress, and the designer should be able to implement it on Wordpress on a later step

```html
<!DOCTYPE html>
<html lang="de">
<head>
<meta charset="utf-8">
<title>tanu-werk – Lösungen</title>
<link rel="stylesheet" href="https://fonts.googleapis.com/css2?family=Roboto:wght@400;500;700&display=swap">
<style>
:root{
  --navy:#111827;
  --navy-2:#151c2d;
  --magenta:#d8279e;
  --purple:#7a5bc9;
  --white:#ffffff;
  --text:#e9ebf1;
}
*{box-sizing:border-box;margin:0;padding:0}
html,body{width:767px;height:1200px;overflow:hidden}
body{background:var(--navy);color:var(--text);font-family:'Roboto',sans-serif;position:relative}

.site-header{position:absolute;top:0;left:0;width:767px;height:47px;display:flex;align-items:center;padding:0 71px}
.brand{display:flex;align-items:center;gap:6px;color:var(--white);font-weight:500;font-size:17px;letter-spacing:.2px}
.brand-dot{width:14px;height:14px;border-radius:50%;border:2px solid var(--magenta)}
.main-nav{margin-left:auto;display:flex;gap:28px}
.main-nav a{color:var(--white);text-decoration:none;font-weight:700;font-size:10px;letter-spacing:.1px}
.main-nav a.active{color:var(--magenta)}

.gradient-rule{position:absolute;left:0;width:767px;height:3px;background:linear-gradient(90deg,var(--purple) 0%,var(--purple) 50%,var(--magenta) 50%,var(--magenta) 100%)}
.rule-top{top:46px}
.rule-bottom{top:1129px}

.hero{position:absolute;top:49px;left:0;width:767px;height:329px}
.hero-copy{position:absolute;left:71px;top:51px;width:298px}
.hero-copy h1{color:var(--white);font-weight:700;font-size:22px;margin-bottom:15px}
.hero-copy p{font-size:9px;line-height:20.3px;text-align:justify;color:var(--white)}
.hero-copy .hl{color:var(--magenta)}
.hero-photo{position:absolute;left:391px;top:0;width:376px;height:329px;
  background:linear-gradient(160deg,#e9a94a 0%,#c77a2c 30%,#5a4632 60%,#c9ccd2 85%,#e6e8ec 100%)}

.solutions{position:absolute;top:378px;left:0;width:767px;height:751px;
  background:radial-gradient(ellipse at 30% 40%,#1f2638 0%,var(--navy-2) 55%,var(--navy) 100%)}
.solutions h2{position:absolute;top:59px;width:100%;text-align:center;color:var(--white);font-weight:500;font-size:12.5px}

.card{position:absolute;top:103px;width:208px;height:589px;border:1.5px solid;border-image:linear-gradient(180deg,var(--purple),var(--magenta)) 1;padding:18px 14px 0 15px}
.card-private{left:63px}
.card-business{left:280px}
.card-community{left:496px}
.card h3{color:var(--magenta);font-weight:700;font-size:16.5px;margin:0 0 10px 6px}
.card ul{list-style:none}
.card li{position:relative;padding-left:11px;font-size:8.8px;line-height:13.2px;color:var(--white)}
.card li::before{content:"";position:absolute;left:0;top:3.5px;width:6px;height:6px;border-radius:50%;border:1px solid var(--magenta);box-shadow:inset 0 0 0 1.2px var(--navy-2);background:var(--magenta)}
.card li.sub{font-size:8px;padding-left:11px;line-height:15.3px}
.card li.sub::before{content:"-";width:auto;height:auto;border:0;box-shadow:none;background:none;color:var(--magenta);top:0;font-size:7px}

.site-footer{position:absolute;top:1132px;left:0;width:767px;height:68px;display:flex;align-items:center;padding:0 66px;font-size:9.3px;color:var(--white)}
.site-footer .links{display:flex;gap:31px;margin-left:42px}
.site-footer .links a{color:var(--white);text-decoration:none}
.social{margin-left:auto;display:flex;gap:7px}
.social span{width:24px;height:24px;border-radius:50%;background:#2a3246}
</style>
</head>
<body>
<header class="site-header">
  <div class="brand"><span class="brand-dot"></span>tanu-werk.de</div>
  <nav class="main-nav">
    <a class="active" href="#">LÖSUNGEN</a>
    <a href="#">UNTERNEHMEN</a>
    <a href="#">SERVICES</a>
    <a href="#">KARRIERE</a>
    <a href="#">KONTAKT</a>
  </nav>
</header>
<div class="gradient-rule rule-top"></div>

<section class="hero">
  <div class="hero-copy">
    <h1>Tanu-werk ist Ihr Partner</h1>
    <p>Wir bieten Lösungen sowohl für <span class="hl">Privatkunden, Geschäftskunden</span> als auch <span class="hl">Kommunen</span> an, die schnell, fair und ohne Eigenleistung zu einer smarten Ladelösung für E-Fahrzeuge kommen möchten.<br>Von der Beratung, über die Installation, Inbetriebnahme bis zur Abrechnung und Wartung bekommen Sie bei tanu-werk alles aus einer Hand. Auf Wunsch vermieten wir auch die Ladetechnik und übernehmen im gewerblichen Bereich die direkte Abrechnung mit dem Nutzer. Für Kommunen bieten wir den kostenfreien Full-Service an und beteiligen die Gemeinden an der Nutzung der Infrastruktur.</p>
  </div>
  <div class="hero-photo" role="img" aria-label="Foto: Frau mit Smartphone lädt ihr Elektroauto bei Sonnenuntergang"></div>
</section>

<section class="solutions">
  <h2>Fragen Sie uns nach der auf Ihre individuellen Bedürfnisse zugeschnittenen Lösung:</h2>

  <article class="card card-private">
    <h3>als Privatkunde</h3>
    <ul>
      <li style="margin-bottom:14px">Bestandsanalyse mit umfangreicher Beratung über die Möglichkeiten der Umsetzung</li>
      <li style="margin-bottom:27px">Prüfung und Übernahme der Anmeldung verfügbarer Fördermöglichkeiten</li>
      <li style="margin-bottom:10px">Auswahl an smarten Wallbox Lösungen, passend für Ihr Fahrzeug und Ihre Bedürfnisse</li>
      <li style="margin-bottom:10px">Installation inkl. aller notwendigen Materialien und Tätigkeiten (Durchbrüche, Erdarbeiten, etc.</li>
      <li style="margin-bottom:10px">Inbetriebnahme und Einweisung in die Ladetechnik</li>
      <li style="margin-bottom:10px">Jährlich technische Wartung nach DGUV3</li>
      <li>Reparaturservice, unter Berücksichtigung der geltenden Garantie Ansprüche</li>
    </ul>
  </article>

  <article class="card card-business">
    <h3>als Geschäftskunde</h3>
    <ul>
      <li style="margin-bottom:5px">Durchführung einer individuellen Bedarfsanalyse inkl. Ermittlung der Anforderungen für:</li>
      <li class="sub">Haus- und Immobilienverwaltungen</li>
      <li class="sub">Dienstleistungs- und Handelsunternehmen</li>
      <li class="sub">Hotel und Beherbergungsbetriebe</li>
      <li class="sub">Parkraum- und Parkhausbetreiber</li>
      <li class="sub" style="margin-bottom:6px">Tourismus, Sport- und Freizeiteinrichtungen</li>
      <li style="margin-bottom:11px">Planung und Projektierung des Installationsaufwands inkl. Materialverbrauch</li>
      <li style="margin-bottom:7px">Leasing oder Kauf der Hardware</li>
      <li style="margin-bottom:16px">Normgerechte Installation der Ladeinfrastruktur inkl. Durchbruch-, Brandschutz- und Erdarbeiten</li>
      <li style="margin-bottom:13px">Bei Bestandsbauten Integration der Ladeinfrastruktur in die Gebäudesystemtechnik und ggf. Anpassung des Netzanschlusses</li>
      <li style="margin-bottom:8px">Inbetriebnahme der Anlage inkl. Prüf- und Messprotokollen</li>
      <li style="margin-bottom:8px">Wiederkehrende technische Prüfung der Anlage nach DGUV 3</li>
      <li style="margin-bottom:7px">Austausch und Reparatur Service</li>
      <li style="margin-bottom:21px">Unterstützung bei der mtl. Nutzungsabrechnung und Einbindung in Ihre vorhandene Abrechnungssysteme</li>
      <li>ODER direkte Abrechnung mit den Nutzern</li>
    </ul>
  </article>

  <article class="card card-community">
    <h3>als Kommune</h3>
    <ul>
      <li style="margin-bottom:23px">Konzeptionierung möglicher Ladeinfrastrukturen innerhalb Ihrer Gemeinde</li>
      <li style="margin-bottom:10px">Planung und Projektsteuerung inkl. sämtlicher behördlicher Genehmigungsverfahren und Beantragung von Fördermitteln</li>
      <li style="margin-bottom:16px">Fachgerechte Installation und Inbetriebnahme</li>
      <li style="margin-bottom:18px">Regelmäßige Wartung gemäß Vorschrift</li>
      <li style="margin-bottom:6px">Reparatur und Kundenservice</li>
      <li style="margin-bottom:23px">Direkte Abrechnung mit dem Nutzer</li>
      <li style="margin-bottom:23px">Beteiligung der Gemeinde am Umsatz</li>
      <li>Möglichkeit der Integration von Bonusprogrammen, mit denen der lokale Einzelhandel beworben wird</li>
    </ul>
  </article>
</section>

<div class="gradient-rule rule-bottom"></div>
<footer class="site-footer">
  <span>©tanu-werk GmbH</span>
  <nav class="links">
    <a href="#">AGB Datenschutzerklarung</a>
    <a href="#">Impressum</a>
    <a href="#">Kontakt</a>
    <a href="#">Karriere</a>
    <a href="#">FAQ</a>
  </nav>
  <div class="social"><span></span><span></span><span></span></div>
</footer>
</body>
</html>
```